Fun A1 2012 family planner using clever typography and block colour

I have been looking for an A1 2012 family planner and I have not been able to find one. Hence I would like help to develop such a planner. I plan to print it on matt paper, portrait orientated. I have attached some reference pictures of our 2011 planner. I like interesting typography, clear clean colours and simple illustration. I need space to write in daily events and need the weeks and days to be clearly delineated from each other. Each day cell needs the date and day in it (please refer to the file uploaded for a visual reference confirming this). Each weekend needs some kind of colour/ typographic delineation. I want a design for a year-at-a-view calendar. I plan to print the planner in Sydney, Australia with brightloomprints.com.au and probably to sell printed copies online. The terms & conditions of this project are that I will own the design concept 100% and in perpetuity worldwide once payment has been made. (NB. The attached Work File in Word contains a rough layout and all months, days and dates all typed up to make for quicker design.)

Target Market(s)

Reasonably well heeled family of 4. 2 parents. 2 kids. 2 pets.

Industry/Entity Type

Events

Requirements
Must have
• The calendar must be portrait (not landscape orientated), A1 size. It will be printed on matt paper by brightloomprints.com.au. It must have months running left to right (Jan-Dec) and day/date cells running top to bottom (refer 2011 planner photos in file uploaded). The day/ date cells must be around 3(w)x2(h)cm - big enough to write daily events in. Weekends must be colour/ typographically delineated. 2012 year must be noted as must "A Pebblegate Inc Project" and web address in fine print bottom left hand left hand corner.
Nice to have
• A Pebblegate Inc logo in bottom left hand corder (perhaps Nimble Owl like: http://www.artmarketly.com/design_submission.aspx?designid=731462). Header/Footer space for customisation (e.g. "Hartono-Quist 2012 Planner" or "XYZ Co 2012 Planner".
Should not have
• The calendar should not use photographs or resemble standard or cheesy wall calendars. No watermarks please.

```html
<!DOCTYPE html>
<html lang="en">
<head>
<meta charset="utf-8">
<title>2012 Year Planner</title>
<link href="https://fonts.googleapis.com/css2?family=Alfa+Slab+One&family=Roboto+Condensed:wght@300;400;700&display=swap" rel="stylesheet">
<style>
:root{
  --jan:#f7941d; --feb:#6670b8; --mar:#ed1c24; --apr:#0f9549;
  --may:#d4521f; --jun:#ed1c24; --jul:#0b5b2e; --aug:#fff200;
  --sep:#39b54a; --oct:#ec1460; --nov:#2e3192; --dec:#1fb07a;
  --ink:#777; --dark:#222; --rule:#cfcfcf; --divider:#e2e2e2;
}
*{margin:0;padding:0;box-sizing:border-box}
html,body{width:847px;height:1200px;overflow:hidden}
body{background:radial-gradient(ellipse at 50% 45%,#ffffff 0%,#fbfbfb 60%,#f1f1f1 100%);font-family:"Roboto Condensed",sans-serif;position:relative}
.planner{position:absolute;left:32px;top:64px;width:777px}
.month-heads{display:grid;grid-template-columns:repeat(12,1fr);height:59px}
.month-head{width:59px;height:59px;background:var(--c);display:flex;align-items:center;justify-content:center;overflow:hidden}
.month-head span{font-family:"Alfa Slab One",serif;font-size:25px;color:#fff;transform:rotate(-52deg);-webkit-text-stroke:1px #111;text-shadow:2px 2px 0 #111;white-space:nowrap;letter-spacing:.5px}
.months{display:grid;grid-template-columns:repeat(12,1fr);margin-top:25px}
.month{border-right:1px solid var(--divider);list-style:none}
.month:last-child{border-right:none}
.day{height:28.7px;border-bottom:1px solid var(--rule);display:flex;align-items:center;justify-content:center}
.date{width:24px;height:24px;display:flex;flex-direction:column;align-items:center;justify-content:center;color:var(--ink);line-height:1}
.date b{font-weight:300;font-size:12px}
.date small{font-size:6px;font-weight:300;margin-top:1px;letter-spacing:.2px}
.weekend .date{background:var(--c);color:#fff}
.credit{position:absolute;left:57px;top:1108px;color:var(--dark)}
.credit .year{font-size:30px;font-weight:700;line-height:1;letter-spacing:1px}
.credit .project{font-size:10px;font-weight:400;margin-top:4px}
</style>
</head>
<body>
<main class="planner">
  <header class="month-heads">
    <div class="month-head" style="--c:var(--jan)"><span>Jan</span></div>
    <div class="month-head" style="--c:var(--feb)"><span>Feb</span></div>
    <div class="month-head" style="--c:var(--mar)"><span>Mar</span></div>
    <div class="month-head" style="--c:var(--apr)"><span>Apr</span></div>
    <div class="month-head" style="--c:var(--may)"><span>May</span></div>
    <div class="month-head" style="--c:var(--jun)"><span>Jun</span></div>
    <div class="month-head" style="--c:var(--jul)"><span>Jul</span></div>
    <div class="month-head" style="--c:var(--aug)"><span>Aug</span></div>
    <div class="month-head" style="--c:var(--sep)"><span>Sep</span></div>
    <div class="month-head" style="--c:var(--oct)"><span>Oct</span></div>
    <div class="month-head" style="--c:var(--nov)"><span>Nov</span></div>
    <div class="month-head" style="--c:var(--dec)"><span>Dec</span></div>
  </header>
  <div class="months">
    <ol class="month" style="--c:var(--jan)">
      <li class="day weekend"><span class="date"><b>01</b><small>SUN</small></span></li>
      <li class="day"><span class="date"><b>02</b><small>MON</small></span></li>
      <li class="day"><span class="date"><b>03</b><small>TUE</small></span></li>
      <li class="day"><span class="date"><b>04</b><small>WED</small></span></li>
      <li class="day"><span class="date"><b>05</b><small>THU</small></span></li>
      <li class="day"><span class="date"><b>06</b><small>FRI</small></span></li>
      <li class="day weekend"><span class="date"><b>07</b><small>SAT</small></span></li>
      <li class="day weekend"><span class="date"><b>08</b><small>SUN</small></span></li>
      <li class="day"><span class="date"><b>09</b><small>MON</small></span></li>
      <li class="day"><span class="date"><b>10</b><small>TUE</small></span></li>
      <li class="day"><span class="date"><b>11</b><small>WED</small></span></li>
      <li class="day"><span class="date"><b>12</b><small>THU</small></span></li>
      <li class="day"><span class="date"><b>13</b><small>FRI</small></span></li>
      <li class="day weekend"><span class="date"><b>14</b><small>SAT</small></span></li>
      <li class="day weekend"><span class="date"><b>15</b><small>SUN</small></span></li>
      <li class="day"><span class="date"><b>16</b><small>MON</small></span></li>
      <li class="day"><span class="date"><b>17</b><small>TUE</small></span></li>
      <li class="day"><span class="date"><b>18</b><small>WED</small></span></li>
      <li class="day"><span class="date"><b>19</b><small>THU</small></span></li>
      <li class="day"><span class="date"><b>20</b><small>FRI</small></span></li>
      <li class="day weekend"><span class="date"><b>21</b><small>SAT</small></span></li>
      <li class="day weekend"><span class="date"><b>22</b><small>SUN</small></span></li>
      <li class="day"><span class="date"><b>23</b><small>MON</small></span></li>
      <li class="day"><span class="date"><b>24</b><small>TUE</small></span></li>
      <li class="day"><span class="date"><b>25</b><small>WED</small></span></li>
      <li class="day"><span class="date"><b>26</b><small>THU</small></span></li>
      <li class="day"><span class="date"><b>27</b><small>FRI</small></span></li>
      <li class="day weekend"><span class="date"><b>28</b><small>SAT</small></span></li>
      <li class="day weekend"><span class="date"><b>29</b><small>SUN</small></span></li>
      <li class="day"><span class="date"><b>30</b><small>MON</small></span></li>
      <li class="day"><span class="date"><b>31</b><small>TUE</small></span></li>
    </ol>
    <ol class="month" style="--c:var(--feb)">
      <li class="day"><span class="date"><b>01</b><small>WED</small></span></li>
      <li class="day"><span class="date"><b>02</b><small>THU</small></span></li>
      <li class="day"><span class="date"><b>03</b><small>FRI</small></span></li>
      <li class="day weekend"><span class="date"><b>04</b><small>SAT</small></span></li>
      <li class="day weekend"><span class="date"><b>05</b><small>SUN</small></span></li>
      <li class="day"><span class="date"><b>06</b><small>MON</small></span></li>
      <li class="day"><span class="date"><b>07</b><small>TUE</small></span></li>
      <li class="day"><span class="date"><b>08</b><small>WED</small></span></li>
      <li class="day"><span class="date"><b>09</b><small>THU</small></span></li>
      <li class="day"><span class="date"><b>10</b><small>FRI</small></span></li>
      <li class="day weekend"><span class="date"><b>11</b><small>SAT</small></span></li>
      <li class="day weekend"><span class="date"><b>12</b><small>SUN</small></span></li>
      <li class="day"><span class="date"><b>13</b><small>MON</small></span></li>
      <li class="day"><span class="date"><b>14</b><small>TUE</small></span></li>
      <li class="day"><span class="date"><b>15</b><small>WED</small></span></li>
      <li class="day"><span class="date"><b>16</b><small>THU</small></span></li>
      <li class="day"><span class="date"><b>17</b><small>FRI</small></span></li>
      <li class="day weekend"><span class="date"><b>18</b><small>SAT</small></span></li>
      <li class="day weekend"><span class="date"><b>19</b><small>SUN</small></span></li>
      <li class="day"><span class="date"><b>20</b><small>MON</small></span></li>
      <li class="day"><span class="date"><b>21</b><small>TUE</small></span></li>
      <li class="day"><span class="date"><b>22</b><small>WED</small></span></li>
      <li class="day"><span class="date"><b>23</b><small>THU</small></span></li>
      <li class="day"><span class="date"><b>24</b><small>FRI</small></span></li>
      <li class="day weekend"><span class="date"><b>25</b><small>SAT</small></span></li>
      <li class="day weekend"><span class="date"><b>26</b><small>SUN</small></span></li>
      <li class="day"><span class="date"><b>27</b><small>MON</small></span></li>
      <li class="day"><span class="date"><b>28</b><small>TUE</small></span></li>
      <li class="day"><span class="date"><b>29</b><small>WED</small></span></li>
    </ol>
    <ol class="month" style="--c:var(--mar)">
      <li class="day"><span class="date"><b>01</b><small>THU</small></span></li>
      <li class="day"><span class="date"><b>02</b><small>FRI</small></span></li>
      <li class="day weekend"><span class="date"><b>03</b><small>SAT</small></span></li>
      <li class="day weekend"><span class="date"><b>04</b><small>SUN</small></span></li>
      <li class="day"><span class="date"><b>05</b><small>MON</small></span></li>
      <li class="day"><span class="date"><b>06</b><small>TUE</small></span></li>
      <li class="day"><span class="date"><b>07</b><small>WED</small></span></li>
      <li class="day"><span class="date"><b>08</b><small>THU</small></span></li>
      <li class="day"><span class="date"><b>09</b><small>FRI</small></span></li>
      <li class="day weekend"><span class="date"><b>10</b><small>SAT</small></span></li>
      <li class="day weekend"><span class="date"><b>11</b><small>SUN</small></span></li>
      <li class="day"><span class="date"><b>12</b><small>MON</small></span></li>
      <li class="day"><span class="date"><b>13</b><small>TUE</small></span></li>
      <li class="day"><span class="date"><b>14</b><small>WED</small></span></li>
      <li class="day"><span class="date"><b>15</b><small>THU</small></span></li>
      <li class="day"><span class="date"><b>16</b><small>FRI</small></span></li>
      <li class="day weekend"><span class="date"><b>17</b><small>SAT</small></span></li>
      <li class="day weekend"><span class="date"><b>18</b><small>SUN</small></span></li>
      <li class="day"><span class="date"><b>19</b><small>MON</small></span></li>
      <li class="day"><span class="date"><b>20</b><small>TUE</small></span></li>
      <li class="day"><span class="date"><b>21</b><small>WED</small></span></li>
      <li class="day"><span class="date"><b>22</b><small>THU</small></span></li>
      <li class="day"><span class="date"><b>23</b><small>FRI</small></span></li>
      <li class="day weekend"><span class="date"><b>24</b><small>SAT</small></span></li>
      <li class="day weekend"><span class="date"><b>25</b><small>SUN</small></span></li>
      <li class="day"><span class="date"><b>26</b><small>MON</small></span></li>
      <li class="day"><span class="date"><b>27</b><small>TUE</small></span></li>
      <li class="day"><span class="date"><b>28</b><small>WED</small></span></li>
      <li class="day"><span class="date"><b>29</b><small>THU</small></span></li>
      <li class="day"><span class="date"><b>30</b><small>FRI</small></span></li>
      <li class="day weekend"><span class="date"><b>31</b><small>SAT</small></span></li>
    </ol>
    <ol class="month" style="--c:var(--apr)">
      <li class="day weekend"><span class="date"><b>01</b><small>SUN</small></span></li>
      <li class="day"><span class="date"><b>02</b><small>MON</small></span></li>
      <li class="day"><span class="date"><b>03</b><small>TUE</small></span></li>
      <li class="day"><span class="date"><b>04</b><small>WED</small></span></li>
      <li class="day"><span class="date"><b>05</b><small>THU</small></span></li>
      <li class="day"><span class="date"><b>06</b><small>FRI</small></span></li>
      <li class="day weekend"><span class="date"><b>07</b><small>SAT</small></span></li>
      <li class="day weekend"><span class="date"><b>08</b><small>SUN</small></span></li>
      <li class="day"><span class="date"><b>09</b><small>MON</small></span></li>
      <li class="day"><span class="date"><b>10</b><small>TUE</small></span></li>
      <li class="day"><span class="date"><b>11</b><small>WED</small></span></li>
      <li class="day"><span class="date"><b>12</b><small>THU</small></span></li>
      <li class="day"><span class="date"><b>13</b><small>FRI</small></span></li>
      <li class="day weekend"><span class="date"><b>14</b><small>SAT</small></span></li>
      <li class="day weekend"><span class="date"><b>15</b><small>SUN</small></span></li>
      <li class="day"><span class="date"><b>16</b><small>MON</small></span></li>
      <li class="day"><span class="date"><b>17</b><small>TUE</small></span></li>
      <li class="day"><span class="date"><b>18</b><small>WED</small></span></li>
      <li class="day"><span class="date"><b>19</b><small>THU</small></span></li>
      <li class="day"><span class="date"><b>20</b><small>FRI</small></span></li>
      <li class="day weekend"><span class="date"><b>21</b><small>SAT</small></span></li>
      <li class="day weekend"><span class="date"><b>22</b><small>SUN</small></span></li>
      <li class="day"><span class="date"><b>23</b><small>MON</small></span></li>
      <li class="day"><span class="date"><b>24</b><small>TUE</small></span></li>
      <li class="day"><span class="date"><b>25</b><small>WED</small></span></li>
      <li class="day"><span class="date"><b>26</b><small>THU</small></span></li>
      <li class="day"><span class="date"><b>27</b><small>FRI</small></span></li>
      <li class="day weekend"><span class="date"><b>28</b><small>SAT</small></span></li>
      <li class="day weekend"><span class="date"><b>29</b><small>SUN</small></span></li>
      <li class="day"><span class="date"><b>30</b><small>MON</small></span></li>
    </ol>
    <ol class="month" style="--c:var(--may)">
      <li class="day"><span class="date"><b>01</b><small>TUE</small></span></li>
      <li class="day"><span class="date"><b>02</b><small>WED</small></span></li>
      <li class="day"><span class="date"><b>03</b><small>THU</small></span></li>
      <li class="day"><span class="date"><b>04</b><small>FRI</small></span></li>
      <li class="day weekend"><span class="date"><b>05</b><small>SAT</small></span></li>
      <li class="day weekend"><span class="date"><b>06</b><small>SUN</small></span></li>
      <li class="day"><span class="date"><b>07</b><small>MON</small></span></li>
      <li class="day"><span class="date"><b>08</b><small>TUE</small></span></li>
      <li class="day"><span class="date"><b>09</b><small>WED</small></span></li>
      <li class="day"><span class="date"><b>10</b><small>THU</small></span></li>
      <li class="day"><span class="date"><b>11</b><small>FRI</small></span></li>
      <li class="day weekend"><span class="date"><b>12</b><small>SAT</small></span></li>
      <li class="day weekend"><span class="date"><b>13</b><small>SUN</small></span></li>
      <li class="day"><span class="date"><b>14</b><small>MON</small></span></li>
      <li class="day"><span class="date"><b>15</b><small>TUE</small></span></li>
      <li class="day"><span class="date"><b>16</b><small>WED</small></span></li>
      <li class="day"><span class="date"><b>17</b><small>THU</small></span></li>
      <li class="day"><span class="date"><b>18</b><small>FRI</small></span></li>
      <li class="day weekend"><span class="date"><b>19</b><small>SAT</small></span></li>
      <li class="day weekend"><span class="date"><b>20</b><small>SUN</small></span></li>
      <li class="day"><span class="date"><b>21</b><small>MON</small></span></li>
      <li class="day"><span class="date"><b>22</b><small>TUE</small></span></li>
      <li class="day"><span class="date"><b>23</b><small>WED</small></span></li>
      <li class="day"><span class="date"><b>24</b><small>THU</small></span></li>
      <li class="day"><span class="date"><b>25</b><small>FRI</small></span></li>
      <li class="day weekend"><span class="date"><b>26</b><small>SAT</small></span></li>
      <li class="day weekend"><span class="date"><b>27</b><small>SUN</small></span></li>
      <li class="day"><span class="date"><b>28</b><small>MON</small></span></li>
      <li class="day"><span class="date"><b>29</b><small>TUE</small></span></li>
      <li class="day"><span class="date"><b>30</b><small>WED</small></span></li>
      <li class="day"><span class="date"><b>31</b><small>THU</small></span></li>
    </ol>
    <ol class="month" style="--c:var(--jun)">
      <li class="day"><span class="date"><b>01</b><small>FRI</small></span></li>
      <li class="day weekend"><span class="date"><b>02</b><small>SAT</small></span></li>
      <li class="day weekend"><span class="date"><b>03</b><small>SUN</small></span></li>
      <li class="day"><span class="date"><b>04</b><small>MON</small></span></li>
      <li class="day"><span class="date"><b>05</b><small>TUE</small></span></li>
      <li class="day"><span class="date"><b>06</b><small>WED</small></span></li>
      <li class="day"><span class="date"><b>07</b><small>THU</small></span></li>
      <li class="day"><span class="date"><b>08</b><small>FRI</small></span></li>
      <li class="day weekend"><span class="date"><b>09</b><small>SAT</small></span></li>
      <li class="day weekend"><span class="date"><b>10</b><small>SUN</small></span></li>
      <li class="day"><span class="date"><b>11</b><small>MON</small></span></li>
      <li class="day"><span class="date"><b>12</b><small>TUE</small></span></li>
      <li class="day"><span class="date"><b>13</b><small>WED</small></span></li>
      <li class="day"><span class="date"><b>14</b><small>THU</small></span></li>
      <li class="day"><span class="date"><b>15</b><small>FRI</small></span></li>
      <li class="day weekend"><span class="date"><b>16</b><small>SAT</small></span></li>
      <li class="day weekend"><span class="date"><b>17</b><small>SUN</small></span></li>
      <li class="day"><span class="date"><b>18</b><small>MON</small></span></li>
      <li class="day"><span class="date"><b>19</b><small>TUE</small></span></li>
      <li class="day"><span class="date"><b>20</b><small>WED</small></span></li>
      <li class="day"><span class="date"><b>21</b><small>THU</small></span></li>
      <li class="day"><span class="date"><b>22</b><small>FRI</small></span></li>
      <li class="day weekend"><span class="date"><b>23</b><small>SAT</small></span></li>
      <li class="day weekend"><span class="date"><b>24</b><small>SUN</small></span></li>
      <li class="day"><span class="date"><b>25</b><small>MON</small></span></li>
      <li class="day"><span class="date"><b>26</b><small>TUE</small></span></li>
      <li class="day"><span class="date"><b>27</b><small>WED</small></span></li>
      <li class="day"><span class="date"><b>28</b><small>THU</small></span></li>
      <li class="day"><span class="date"><b>29</b><small>FRI</small></span></li>
      <li class="day weekend"><span class="date"><b>30</b><small>SAT</small></span></li>
    </ol>
    <ol class="month" style="--c:var(--jul)">
      <li class="day weekend"><span class="date"><b>01</b><small>SUN</small></span></li>
      <li class="day"><span class="date"><b>02</b><small>MON</small></span></li>
      <li class="day"><span class="date"><b>03</b><small>TUE</small></span></li>
      <li class="day"><span class="date"><b>04</b><small>WED</small></span></li>
      <li class="day"><span class="date"><b>05</b><small>THU</small></span></li>
      <li class="day"><span class="date"><b>06</b><small>FRI</small></span></li>
      <li class="day weekend"><span class="date"><b>07</b><small>SAT</small></span></li>
      <li class="day weekend"><span class="date"><b>08</b><small>SUN</small></span></li>
      <li class="day"><span class="date"><b>09</b><small>MON</small></span></li>
      <li class="day"><span class="date"><b>10</b><small>TUE</small></span></li>
      <li class="day"><span class="date"><b>11</b><small>WED</small></span></li>
      <li class="day"><span class="date"><b>12</b><small>THU</small></span></li>
      <li class="day"><span class="date"><b>13</b><small>FRI</small></span></li>
      <li class="day weekend"><span class="date"><b>14</b><small>SAT</small></span></li>
      <li class="day weekend"><span class="date"><b>15</b><small>SUN</small></span></li>
      <li class="day"><span class="date"><b>16</b><small>MON</small></span></li>
      <li class="day"><span class="date"><b>17</b><small>TUE</small></span></li>
      <li class="day"><span class="date"><b>18</b><small>WED</small></span></li>
      <li class="day"><span class="date"><b>19</b><small>THU</small></span></li>
      <li class="day"><span class="date"><b>20</b><small>FRI</small></span></li>
      <li class="day weekend"><span class="date"><b>21</b><small>SAT</small></span></li>
      <li class="day weekend"><span class="date"><b>22</b><small>SUN</small></span></li>
      <li class="day"><span class="date"><b>23</b><small>MON</small></span></li>
      <li class="day"><span class="date"><b>24</b><small>TUE</small></span></li>
      <li class="day"><span class="date"><b>25</b><small>WED</small></span></li>
      <li class="day"><span class="date"><b>26</b><small>THU</small></span></li>
      <li class="day"><span class="date"><b>27</b><small>FRI</small></span></li>
      <li class="day weekend"><span class="date"><b>28</b><small>SAT</small></span></li>
      <li class="day weekend"><span class="date"><b>29</b><small>SUN</small></span></li>
      <li class="day"><span class="date"><b>30</b><small>MON</small></span></li>
      <li class="day"><span class="date"><b>31</b><small>TUE</small></span></li>
    </ol>
    <ol class="month" style="--c:var(--aug)">
      <li class="day"><span class="date"><b>01</b><small>WED</small></span></li>
      <li class="day"><span class="date"><b>02</b><small>THU</small></span></li>
      <li class="day"><span class="date"><b>03</b><small>FRI</small></span></li>
      <li class="day weekend"><span class="date"><b>04</b><small>SAT</small></span></li>
      <li class="day weekend"><span class="date"><b>05</b><small>SUN</small></span></li>
      <li class="day"><span class="date"><b>06</b><small>MON</small></span></li>
      <li class="day"><span class="date"><b>07</b><small>TUE</small></span></li>
      <li class="day"><span class="date"><b>08</b><small>WED</small></span></li>
      <li class="day"><span class="date"><b>09</b><small>THU</small></span></li>
      <li class="day"><span class="date"><b>10</b><small>FRI</small></span></li>
      <li class="day weekend"><span class="date"><b>11</b><small>SAT</small></span></li>
      <li class="day weekend"><span class="date"><b>12</b><small>SUN</small></span></li>
      <li class="day"><span class="date"><b>13</b><small>MON</small></span></li>
      <li class="day"><span class="date"><b>14</b><small>TUE</small></span></li>
      <li class="day"><span class="date"><b>15</b><small>WED</small></span></li>
      <li class="day"><span class="date"><b>16</b><small>THU</small></span></li>
      <li class="day"><span class="date"><b>17</b><small>FRI</small></span></li>
      <li class="day weekend"><span class="date"><b>18</b><small>SAT</small></span></li>
      <li class="day weekend"><span class="date"><b>19</b><small>SUN</small></span></li>
      <li class="day"><span class="date"><b>20</b><small>MON</small></span></li>
      <li class="day"><span class="date"><b>21</b><small>TUE</small></span></li>
      <li class="day"><span class="date"><b>22</b><small>WED</small></span></li>
      <li class="day"><span class="date"><b>23</b><small>THU</small></span></li>
      <li class="day"><span class="date"><b>24</b><small>FRI</small></span></li>
      <li class="day weekend"><span class="date"><b>25</b><small>SAT</small></span></li>
      <li class="day weekend"><span class="date"><b>26</b><small>SUN</small></span></li>
      <li class="day"><span class="date"><b>27</b><small>MON</small></span></li>
      <li class="day"><span class="date"><b>28</b><small>TUE</small></span></li>
      <li class="day"><span class="date"><b>29</b><small>WED</small></span></li>
      <li class="day"><span class="date"><b>30</b><small>THU</small></span></li>
      <li class="day"><span class="date"><b>31</b><small>FRI</small></span></li>
    </ol>
    <ol class="month" style="--c:var(--sep)">
      <li class="day weekend"><span class="date"><b>01</b><small>SAT</small></span></li>
      <li class="day weekend"><span class="date"><b>02</b><small>SUN</small></span></li>
      <li class="day"><span class="date"><b>03</b><small>MON</small></span></li>
      <li class="day"><span class="date"><b>04</b><small>TUE</small></span></li>
      <li class="day"><span class="date"><b>05</b><small>WED</small></span></li>
      <li class="day"><span class="date"><b>06</b><small>THU</small></span></li>
      <li class="day"><span class="date"><b>07</b><small>FRI</small></span></li>
      <li class="day weekend"><span class="date"><b>08</b><small>SAT</small></span></li>
      <li class="day weekend"><span class="date"><b>09</b><small>SUN</small></span></li>
      <li class="day"><span class="date"><b>10</b><small>MON</small></span></li>
      <li class="day"><span class="date"><b>11</b><small>TUE</small></span></li>
      <li class="day"><span class="date"><b>12</b><small>WED</small></span></li>
      <li class="day"><span class="date"><b>13</b><small>THU</small></span></li>
      <li class="day"><span class="date"><b>14</b><small>FRI</small></span></li>
      <li class="day weekend"><span class="date"><b>15</b><small>SAT</small></span></li>
      <li class="day weekend"><span class="date"><b>16</b><small>SUN</small></span></li>
      <li class="day"><span class="date"><b>17</b><small>MON</small></span></li>
      <li class="day"><span class="date"><b>18</b><small>TUE</small></span></li>
      <li class="day"><span class="date"><b>19</b><small>WED</small></span></li>
      <li class="day"><span class="date"><b>20</b><small>THU</small></span></li>
      <li class="day"><span class="date"><b>21</b><small>FRI</small></span></li>
      <li class="day weekend"><span class="date"><b>22</b><small>SAT</small></span></li>
      <li class="day weekend"><span class="date"><b>23</b><small>SUN</small></span></li>
      <li class="day"><span class="date"><b>24</b><small>MON</small></span></li>
      <li class="day"><span class="date"><b>25</b><small>TUE</small></span></li>
      <li class="day"><span class="date"><b>26</b><small>WED</small></span></li>
      <li class="day"><span class="date"><b>27</b><small>THU</small></span></li>
      <li class="day"><span class="date"><b>28</b><small>FRI</small></span></li>
      <li class="day weekend"><span class="date"><b>29</b><small>SAT</small></span></li>
      <li class="day weekend"><span class="date"><b>30</b><small>SUN</small></span></li>
    </ol>
    <ol class="month" style="--c:var(--oct)">
      <li class="day"><span class="date"><b>01</b><small>MON</small></span></li>
      <li class="day"><span class="date"><b>02</b><small>TUE</small></span></li>
      <li class="day"><span class="date"><b>03</b><small>WED</small></span></li>
      <li class="day"><span class="date"><b>04</b><small>THU</small></span></li>
      <li class="day"><span class="date"><b>05</b><small>FRI</small></span></li>
      <li class="day weekend"><span class="date"><b>06</b><small>SAT</small></span></li>
      <li class="day weekend"><span class="date"><b>07</b><small>SUN</small></span></li>
      <li class="day"><span class="date"><b>08</b><small>MON</small></span></li>
      <li class="day"><span class="date"><b>09</b><small>TUE</small></span></li>
      <li class="day"><span class="date"><b>10</b><small>WED</small></span></li>
      <li class="day"><span class="date"><b>11</b><small>THU</small></span></li>
      <li class="day"><span class="date"><b>12</b><small>FRI</small></span></li>
      <li class="day weekend"><span class="date"><b>13</b><small>SAT</small></span></li>
      <li class="day weekend"><span class="date"><b>14</b><small>SUN</small></span></li>
      <li class="day"><span class="date"><b>15</b><small>MON</small></span></li>
      <li class="day"><span class="date"><b>16</b><small>TUE</small></span></li>
      <li class="day"><span class="date"><b>17</b><small>WED</small></span></li>
      <li class="day"><span class="date"><b>18</b><small>THU</small></span></li>
      <li class="day"><span class="date"><b>19</b><small>FRI</small></span></li>
      <li class="day weekend"><span class="date"><b>20</b><small>SAT</small></span></li>
      <li class="day weekend"><span class="date"><b>21</b><small>SUN</small></span></li>
      <li class="day"><span class="date"><b>22</b><small>MON</small></span></li>
      <li class="day"><span class="date"><b>23</b><small>TUE</small></span></li>
      <li class="day"><span class="date"><b>24</b><small>WED</small></span></li>
      <li class="day"><span class="date"><b>25</b><small>THU</small></span></li>
      <li class="day"><span class="date"><b>26</b><small>FRI</small></span></li>
      <li class="day weekend"><span class="date"><b>27</b><small>SAT</small></span></li>
      <li class="day weekend"><span class="date"><b>28</b><small>SUN</small></span></li>
      <li class="day"><span class="date"><b>29</b><small>MON</small></span></li>
      <li class="day"><span class="date"><b>30</b><small>TUE</small></span></li>
      <li class="day"><span class="date"><b>31</b><small>WED</small></span></li>
    </ol>
    <ol class="month" style="--c:var(--nov)">
      <li class="day"><span class="date"><b>01</b><small>THU</small></span></li>
      <li class="day"><span class="date"><b>02</b><small>FRI</small></span></li>
      <li class="day weekend"><span class="date"><b>03</b><small>SAT</small></span></li>
      <li class="day weekend"><span class="date"><b>04</b><small>SUN</small></span></li>
      <li class="day"><span class="date"><b>05</b><small>MON</small></span></li>
      <li class="day"><span class="date"><b>06</b><small>TUE</small></span></li>
      <li class="day"><span class="date"><b>07</b><small>WED</small></span></li>
      <li class="day"><span class="date"><b>08</b><small>THU</small></span></li>
      <li class="day"><span class="date"><b>09</b><small>FRI</small></span></li>
      <li class="day weekend"><span class="date"><b>10</b><small>SAT</small></span></li>
      <li class="day weekend"><span class="date"><b>11</b><small>SUN</small></span></li>
      <li class="day"><span class="date"><b>12</b><small>MON</small></span></li>
      <li class="day"><span class="date"><b>13</b><small>TUE</small></span></li>
      <li class="day"><span class="date"><b>14</b><small>WED</small></span></li>
      <li class="day"><span class="date"><b>15</b><small>THU</small></span></li>
      <li class="day"><span class="date"><b>16</b><small>FRI</small></span></li>
      <li class="day weekend"><span class="date"><b>17</b><small>SAT</small></span></li>
      <li class="day weekend"><span class="date"><b>18</b><small>SUN</small></span></li>
      <li class="day"><span class="date"><b>19</b><small>MON</small></span></li>
      <li class="day"><span class="date"><b>20</b><small>TUE</small></span></li>
      <li class="day"><span class="date"><b>21</b><small>WED</small></span></li>
      <li class="day"><span class="date"><b>22</b><small>THU</small></span></li>
      <li class="day"><span class="date"><b>23</b><small>FRI</small></span></li>
      <li class="day weekend"><span class="date"><b>24</b><small>SAT</small></span></li>
      <li class="day weekend"><span class="date"><b>25</b><small>SUN</small></span></li>
      <li class="day"><span class="date"><b>26</b><small>MON</small></span></li>
      <li class="day"><span class="date"><b>27</b><small>TUE</small></span></li>
      <li class="day"><span class="date"><b>28</b><small>WED</small></span></li>
      <li class="day"><span class="date"><b>29</b><small>THU</small></span></li>
      <li class="day"><span class="date"><b>30</b><small>FRI</small></span></li>
    </ol>
    <ol class="month" style="--c:var(--dec)">
      <li class="day weekend"><span class="date"><b>01</b><small>SAT</small></span></li>
      <li class="day weekend"><span class="date"><b>02</b><small>SUN</small></span></li>
      <li class="day"><span class="date"><b>03</b><small>MON</small></span></li>
      <li class="day"><span class="date"><b>04</b><small>TUE</small></span></li>
      <li class="day"><span class="date"><b>05</b><small>WED</small></span></li>
      <li class="day"><span class="date"><b>06</b><small>THU</small></span></li>
      <li class="day"><span class="date"><b>07</b><small>FRI</small></span></li>
      <li class="day weekend"><span class="date"><b>08</b><small>SAT</small></span></li>
      <li class="day weekend"><span class="date"><b>09</b><small>SUN</small></span></li>
      <li class="day"><span class="date"><b>10</b><small>MON</small></span></li>
      <li class="day"><span class="date"><b>11</b><small>TUE</small></span></li>
      <li class="day"><span class="date"><b>12</b><small>WED</small></span></li>
      <li class="day"><span class="date"><b>13</b><small>THU</small></span></li>
      <li class="day"><span class="date"><b>14</b><small>FRI</small></span></li>
      <li class="day weekend"><span class="date"><b>15</b><small>SAT</small></span></li>
      <li class="day weekend"><span class="date"><b>16</b><small>SUN</small></span></li>
      <li class="day"><span class="date"><b>17</b><small>MON</small></span></li>
      <li class="day"><span class="date"><b>18</b><small>TUE</small></span></li>
      <li class="day"><span class="date"><b>19</b><small>WED</small></span></li>
      <li class="day"><span class="date"><b>20</b><small>THU</small></span></li>
      <li class="day"><span class="date"><b>21</b><small>FRI</small></span></li>
      <li class="day weekend"><span class="date"><b>22</b><small>SAT</small></span></li>
      <li class="day weekend"><span class="date"><b>23</b><small>SUN</small></span></li>
      <li class="day"><span class="date"><b>24</b><small>MON</small></span></li>
      <li class="day"><span class="date"><b>25</b><small>TUE</small></span></li>
      <li class="day"><span class="date"><b>26</b><small>WED</small></span></li>
      <li class="day"><span class="date"><b>27</b><small>THU</small></span></li>
      <li class="day"><span class="date"><b>28</b><small>FRI</small></span></li>
      <li class="day weekend"><span class="date"><b>29</b><small>SAT</small></span></li>
      <li class="day weekend"><span class="date"><b>30</b><small>SUN</small></span></li>
      <li class="day"><span class="date"><b>31</b><small>MON</small></span></li>
    </ol>
  </div>
</main>
<footer class="credit">
  <div class="year">2012</div>
  <div class="project">A Pebblegate Inc Project</div>
</footer>
</body>
</html>
```